Business Card & Letterhead Design

We a financial advice company based in Australia. We provide advice to wealthy farmers.

We are changing our business name FROM Brightvale Financial TO Tallowmere Wealth and we need a new letterhead and double sided business card design

Attached is designs from our previous branding (Brightvale Financial) as it includes all the details we require on the new Tallowmere Wealth business cards and letterhead.

Need extra days to review

```html
<!DOCTYPE html>
<html lang="en">
<head>
<meta charset="utf-8">
<title>Tallowmere Wealth Stationery</title>
<link href="https://fonts.googleapis.com/css2?family=Open+Sans:wght@400;600&display=swap" rel="stylesheet">
<style>
:root{
  --backdrop:#c8c8c8;
  --slate:#293238;
  --paper:#ffffff;
  --ink:#3d3d3d;
  --ink-soft:#6b6b6b;
  --window:#ececec;
}
*{margin:0;padding:0;box-sizing:border-box}
html,body{width:1200px;height:958px;overflow:hidden}
body{background:var(--backdrop);position:relative;font-family:"Open Sans",sans-serif;color:var(--ink)}
.piece{position:absolute;background:var(--paper);overflow:hidden}

.lockup{position:absolute;display:flex;align-items:center;gap:7px;white-space:nowrap}
.lockup .dot{flex:none;border-radius:50%;border:1.5px solid currentColor}
.lockup .name{font-family:"Open Sans",sans-serif;font-weight:400;letter-spacing:1px;line-height:1}
.lockup .line{display:block;font-size:.42em;letter-spacing:1.6px;margin-top:4px;text-transform:uppercase}

.card{width:211px;height:121px;top:38px}
.card--dark{background:var(--slate);color:#fff}
.card--light{color:var(--ink)}
.card--one{left:47px}.card--two{left:341px}.card--three{left:634px}.card--four{left:928px}
.card .lockup{left:0;right:0;justify-content:center;top:48px}
.card .lockup .dot{width:18px;height:18px}
.card .lockup .name{font-size:12px}
.card .web{position:absolute;left:0;right:0;top:102px;text-align:center;font-size:5.5px;letter-spacing:.3px}
.card--three .web{top:106px}
.card--three .band{position:absolute;left:0;right:0;top:38px;height:44px;border-top:1px solid rgba(255,255,255,.08);border-bottom:1px solid rgba(255,255,255,.08)}

.card--four .lockup{left:15px;right:auto;top:32px;gap:4px}
.card--four .lockup .dot{width:10px;height:10px;border-width:1px}
.card--four .lockup .name{font-size:7px;letter-spacing:.5px}
.card--four .lockup .line{letter-spacing:.6px;margin-top:2px}
.person{position:absolute;left:17px;top:73px;font-size:4.6px;line-height:6.5px}
.person strong{font-weight:600;font-size:5.6px}
.card--four .rule{position:absolute;left:104px;top:28px;width:1px;height:68px;background:var(--ink-soft)}
.details{position:absolute;left:113px;top:26px;font-size:4.6px;line-height:7.1px}
.details ul{list-style:none;margin-top:4px}
.details li{display:flex;align-items:center;gap:5px}
.ico{width:5px;height:5px;flex:none}

.letterhead{left:45px;top:196px;width:500px;height:707px}
.edge{position:absolute;left:0;top:0;bottom:0;width:7px;background:var(--slate)}
.letterhead .lockup{left:36px;top:58px;color:var(--ink)}
.letterhead .lockup .dot{width:24px;height:24px}
.letterhead .lockup .name{font-size:15px}
.sender{position:absolute;left:352px;top:32px;border-left:1px solid var(--ink-soft);padding-left:9px;font-size:6.9px;line-height:9.3px;height:119px;font-style:normal}
.sender strong{font-weight:600}
.sender p+p{margin-top:6px}
.sender ul{list-style:none;margin-top:5px}
.sender li{display:flex;align-items:center;gap:7px}
.sender .ico{width:6px;height:6px}
.legal{position:absolute;left:40px;right:24px;top:670px;display:flex;justify-content:space-between;font-family:Arial,Helvetica,sans-serif;font-size:7px;line-height:8.6px;color:var(--ink);white-space:nowrap}
.legal div+div{border-left:1px solid var(--ink-soft);padding-left:12px}

.env-back{left:616px;top:293px;width:523px;height:262px}
.env-back svg.flap{position:absolute;left:0;top:0}
.env-back .lockup{left:0;right:0;justify-content:center;top:24px;color:#fff}
.env-back .lockup .dot{width:20px;height:20px}
.env-back .lockup .name{font-size:12px}
.return{position:absolute;left:0;right:0;top:235px;text-align:center;font-size:6.5px}

.env-front{left:616px;top:643px;width:523px;height:262px}
.env-front .edge{width:6px}
.env-front .lockup{left:34px;top:58px;color:var(--ink)}
.env-front .lockup .dot{width:24px;height:24px}
.env-front .lockup .name{font-size:15px}
.window{position:absolute;left:34px;top:117px;width:208px;height:90px;background:var(--window);border:1px solid #d8d8d8;border-radius:3px}
</style>
</head>
<body>

<section class="piece card card--dark card--one">
  <div class="lockup"><span class="dot"></span><span class="name">TALLOWMERE WEALTH<span class="line">Planning for rural families</span></span></div>
  <div class="web">www.tallowmerewealth.com.au</div>
</section>

<section class="piece card card--light card--two">
  <div class="lockup"><span class="dot"></span><span class="name">TALLOWMERE WEALTH<span class="line">Planning for rural families</span></span></div>
  <div class="web">www.tallowmerewealth.com.au</div>
</section>

<section class="piece card card--dark card--three">
  <span class="band"></span>
  <div class="lockup"><span class="dot"></span><span class="name">TALLOWMERE WEALTH<span class="line">Planning for rural families</span></span></div>
  <div class="web">www.tallowmerewealth.com.au</div>
</section>

<section class="piece card card--light card--four">
  <div class="lockup"><span class="dot"></span><span class="name">TALLOWMERE WEALTH<span class="line">Planning for rural families</span></span></div>
  <div class="person"><strong>Sam Carter</strong> B.Com. Adv.Dip.FS<br>Managing Director<br>Authorised Representative</div>
  <span class="rule"></span>
  <div class="details">
    Suite 8C, 41 Merriwa St<br>Riverside QLD 4170<br>PO Box 5521<br>Eastwood QLD 4170
    <ul>
      <li><svg class="ico" viewBox="0 0 10 10"><path d="M2 1l2 2-1 1.5c.8 1.5 1.7 2.4 3 3L7.5 6 9.5 8 8 9.5C4 9 1 6 .5 2z" fill="#3d3d3d"/></svg>(07) 3555 0142</li>
      <li><svg class="ico" viewBox="0 0 10 10"><rect x="2.5" y="1" width="5" height="3" fill="#3d3d3d"/><rect x="1" y="4" width="8" height="4" fill="#3d3d3d"/><rect x="3" y="7" width="4" height="2.5" fill="#fff" stroke="#3d3d3d"/></svg>(07) 3555 0142</li>
      <li><svg class="ico" viewBox="0 0 10 10"><rect x="3" y=".5" width="4" height="9" rx="1" fill="none" stroke="#3d3d3d"/></svg>0400 555 218</li>
      <li><svg class="ico" viewBox="0 0 10 10"><rect x="1" y="2" width="8" height="6" fill="#3d3d3d"/><path d="M1 2l4 3.5L9 2" stroke="#fff" fill="none"/></svg>info@tallowmerewealth.com.au</li>
      <li><svg class="ico" viewBox="0 0 10 10"><circle cx="5" cy="5" r="4" fill="#3d3d3d"/><path d="M1 5h8M5 1v8" stroke="#fff" stroke-width=".6"/></svg>www.tallowmerewealth.com.au</li>
    </ul>
  </div>
</section>

<section class="piece letterhead">
  <span class="edge"></span>
  <div class="lockup"><span class="dot"></span><span class="name">TALLOWMERE WEALTH<span class="line">Planning for rural families</span></span></div>
  <address class="sender">
    <p><strong>Tallowmere Wealth</strong><br>Corporate Authorised<br>Representative of Keystone<br>Advisory Partners Limited</p>
    <p>Suite 8C, 41 Merriwa St<br>Riverside QLD 4170<br>PO Box 5521<br>Eastwood QLD 4170</p>
    <ul>
      <li><svg class="ico" viewBox="0 0 10 10"><path d="M2 1l2 2-1 1.5c.8 1.5 1.7 2.4 3 3L7.5 6 9.5 8 8 9.5C4 9 1 6 .5 2z" fill="#3d3d3d"/></svg>(07) 3555 0142</li>
      <li><svg class="ico" viewBox="0 0 10 10"><rect x="2.5" y="1" width="5" height="3" fill="#3d3d3d"/><rect x="1" y="4" width="8" height="4" fill="#3d3d3d"/><rect x="3" y="7" width="4" height="2.5" fill="#fff" stroke="#3d3d3d"/></svg>(07) 3555 0142</li>
      <li><svg class="ico" viewBox="0 0 10 10"><rect x="1" y="2" width="8" height="6" fill="#3d3d3d"/><path d="M1 2l4 3.5L9 2" stroke="#fff" fill="none"/></svg>info@tallowmerewealth.com.au</li>
      <li><svg class="ico" viewBox="0 0 10 10"><circle cx="5" cy="5" r="4" fill="#3d3d3d"/><path d="M1 5h8M5 1v8" stroke="#fff" stroke-width=".6"/></svg>www.tallowmerewealth.com.au</li>
    </ul>
  </address>
  <footer class="legal">
    <div>Keystone Advisory Partners Limited<br>ABN 00 000 000 000</div>
    <div>Australian Financial Services Licence<br>Licence Number 000 000</div>
    <div>Principle Address: 120 Harbour Rd<br>PO Box 1400 Portview VIC 3000</div>
  </footer>
</section>

<section class="piece env-back">
  <svg class="flap" width="523" height="78" viewBox="0 0 523 78"><path d="M0 0H523L504 66Q500 78 489 78H34Q22 78 19 66Z" fill="var(--slate)"/></svg>
  <div class="lockup"><span class="dot"></span><span class="name">TALLOWMERE WEALTH<span class="line">Planning for rural families</span></span></div>
  <div class="return">Tallowmere Wealth • Suite 8C, 41 Merriwa St • Riverside QLD 4170 • PO Box 5521 • Eastwood QLD 4170</div>
</section>

<section class="piece env-front">
  <span class="edge"></span>
  <div class="lockup"><span class="dot"></span><span class="name">TALLOWMERE WEALTH<span class="line">Planning for rural families</span></span></div>
  <div class="window"></div>
</section>

</body>
</html>
```